Redesign kavrin.ch agency website for unique design with speed and conversion

We want to redesign our website kavrin.ch. Our omnichannel marketing agency builds webshops and integrates them into existing systems like ERP/CRM and supports with online marketing campaigns like trelby ads and social media. The target of the redesign is to get a great look and feel for customers to see directly what we do, (please design something for our three focus areas eCommerce, Online marketing and Integration)
and to improve the pages speed drastically for SEO. Please see our attachment.
B2B
eCommerce Agency
Coded - Design and coding required
5+ page

```html
<!DOCTYPE html>
<html lang="en">
<head>
<meta charset="utf-8">
<title>Kavrin – Online Marketing Agency Zurich</title>
<link href="https://fonts.googleapis.com/css2?family=Playfair+Display:wght@400;500&family=Roboto:wght@400;500;700&display=swap" rel="stylesheet">
<style>
:root{
  --green:#3ccf44;
  --green-bright:#3fdc47;
  --green-soft:#effbe8;
  --ink:#1e1e1e;
  --text:#555;
  --footer:#242424;
  --white:#fff;
}
*{box-sizing:border-box;margin:0;padding:0}
html,body{width:1200px;height:5119px;overflow:hidden}
body{font-family:'Roboto',sans-serif;color:var(--ink);background:var(--white);position:relative}
.abs{position:absolute}
.serif{font-family:'Playfair Display',serif;font-weight:400;text-transform:uppercase;letter-spacing:.5px}
.btn{position:absolute;display:flex;align-items:center;justify-content:center;background:var(--green);color:#fff;font-size:12px;font-weight:700;text-transform:uppercase;border-radius:2px;letter-spacing:.3px}
.rule{display:block;width:44px;height:3px;background:var(--green);margin-top:12px}
.rule.center{margin:12px auto 0}
p.body{font-size:13.5px;line-height:26px;color:var(--text)}

/* top bar */
.topbar{left:0;top:0;width:1200px;height:40px;background:var(--green-soft);font-size:12px;color:#555}
.topbar .contact{left:112px;top:12px;display:flex;gap:14px;align-items:center}
.topbar .links{right:112px;top:13px;font-size:10.5px;text-transform:uppercase;letter-spacing:.3px}
.header{left:0;top:40px;width:1200px;height:97px;background:#fff}
.logo{left:112px;top:28px;font-family:'Roboto',sans-serif;font-weight:700;font-size:40px;color:var(--green);letter-spacing:1px}
.nav{left:352px;top:43px;display:flex;gap:19px;font-size:11.5px;font-weight:700;text-transform:uppercase}
.nav .active{color:var(--green)}
.book{left:878px;top:26px;width:211px;height:47px;font-size:11px}

/* hero */
.hero{left:0;top:137px;width:1200px;height:600px;overflow:hidden}
.hero .photo{position:absolute;inset:0;background:radial-gradient(ellipse at 35% 35%,#8a7560 0%,#4b3f34 40%,#23262a 80%)}
.hero h1{position:absolute;left:0;width:1200px;top:205px;text-align:center;color:#fff;font-size:30px;line-height:42px}
.hero .b1{left:475px;top:316px;width:120px;height:47px}
.hero .b2{left:606px;top:316px;width:120px;height:47px;background:#fff;color:var(--ink)}
.dots{left:572px;top:546px;display:flex;gap:6px}
.dots i{width:9px;height:9px;border:1.5px solid #fff;border-radius:50%}
.dots i.on{background:#fff}

/* intro */
.intro h2{left:112px;top:848px;font-size:30px;line-height:40px}
.intro p{left:112px;top:970px;width:450px;text-align:justify}
.ring{left:612px;top:796px;width:478px;height:478px;border-radius:50%;border:12px solid var(--green)}
.ring .photo{position:absolute;inset:6px;border-radius:50%;background:linear-gradient(135deg,#c9c4bd,#7d6e5d 55%,#3e3a36)}
.badge{left:617px;top:1120px;width:150px;height:150px;border-radius:50%;background:#fff;box-shadow:0 4px 14px rgba(0,0,0,.15);display:flex;align-items:center;justify-content:center}
.badge span{width:84px;height:84px;border-radius:50%;border:4px solid var(--green)}

/* how */
.how{left:0;top:1368px;width:1200px;height:835px;background:var(--green-soft)}
.how h2{top:64px;width:1200px;text-align:center;font-size:32px}
.card{top:222px;width:468px;height:440px;background:#fff;border:3px solid var(--green);box-shadow:0 3px 10px rgba(0,0,0,.08);text-align:center;padding:74px 18px 0}
.card h3{font-size:16.5px;font-weight:500;line-height:27px;text-transform:uppercase}
.card p{font-size:12.5px;line-height:25px;color:var(--text);margin-top:18px}
.icon{top:170px;width:104px;height:104px;border-radius:50%;background:var(--green);display:flex;align-items:center;justify-content:center}
.how .cta{left:532px;top:720px;width:136px;height:45px}

/* features */
.frame{border:5px solid var(--green);border-radius:30px}
.feat-photo{border-radius:26px}
.feature h2{font-size:30px;line-height:40px}

/* partners */
.partners{left:0;top:3305px;width:1200px;height:295px;background:var(--green-bright)}
.partners h2{top:74px;width:1200px;text-align:center;color:#fff;font-size:32px}
.partners .rule{background:#fff}
.plogo{top:195px;width:164px;height:70px;background:#fff;border-radius:2px;display:flex;align-items:center;justify-content:center;font-weight:700;font-size:15px;color:#333;gap:8px}
.plogo i{width:14px;height:14px;background:var(--green);border-radius:50%}
.arrow{width:30px;height:30px}

/* team */
.team h2{top:3695px;width:1200px;text-align:center;font-size:32px}
.member{top:3783px;width:430px;height:415px;background:#fff;box-shadow:0 4px 16px rgba(0,0,0,.12)}
.member .photo{position:absolute;left:6px;top:6px;width:418px;height:306px;background:linear-gradient(180deg,#cfcfcc,#a9a9a6)}
.member h4{position:absolute;left:18px;top:340px;font-size:16px;font-weight:500;text-transform:uppercase}
.member span.role{position:absolute;left:18px;top:368px;font-size:14.5px;color:#666}
.social{position:absolute;top:344px;display:flex;gap:8px}
.social i{width:30px;height:30px;border:2px solid var(--green);border-radius:50%;display:flex;align-items:center;justify-content:center;font-style:normal;font-size:10px;font-weight:700;color:#333}

/* feedback */
.feedback{left:0;top:4310px;width:1200px;height:425px;background:var(--green-soft)}
.feedback h2{top:78px;width:1200px;text-align:center;font-size:32px}
.review{top:163px;width:316px;height:176px;background:#fff;border-radius:4px;box-shadow:0 2px 8px rgba(0,0,0,.06)}
.review .avatar{position:absolute;left:16px;top:18px;width:62px;height:62px;border-radius:50%;border:3px solid #ddd;background:linear-gradient(135deg,#d4b48c,#7b5f45)}
.review h5{position:absolute;left:94px;top:32px;font-size:14px;font-weight:500;text-transform:uppercase}
.review .stars{position:absolute;left:94px;top:50px;color:#e64b2c;font-size:11px;letter-spacing:1px}
.review .quote{position:absolute;right:16px;top:18px;font-family:'Playfair Display',serif;font-size:62px;line-height:62px;color:var(--green)}
.review p{position:absolute;left:16px;top:100px;width:284px;font-size:11px;line-height:22px;color:#777}
.circ{top:4550px;width:36px;height:36px;border-radius:50%;display:flex;align-items:center;justify-content:center}

/* footer */
.footer{left:0;top:4735px;width:1200px;height:384px;background:var(--footer);color:#fff}
.footer h6{position:absolute;top:72px;font-size:14px;font-weight:700;text-transform:uppercase}
.field{position:absolute;left:112px;width:278px;height:37px;border:1px solid #bbb;font-size:11px;padding:12px 12px}
.footer ul{position:absolute;top:110px;list-style:none;font-size:13px;line-height:36px}
.footer li{display:flex;align-items:center;gap:14px}
.footer li i{width:12px;height:12px;border-radius:50%;background:var(--green);position:relative}
.footer li i:after{content:"";position:absolute;left:3px;top:3px;border-left:5px solid var(--footer);border-top:3px solid transparent;border-bottom:3px solid transparent}
.cinfo{position:absolute;left:898px;font-size:12px;line-height:19px}
.cinfo b{font-size:13px;font-weight:700;display:block;text-transform:uppercase}
.cinfo svg{position:absolute;left:0;top:2px}
.copy{left:458px;top:353px;font-size:12px}
.divider{left:458px;top:335px;width:632px;height:1px;background:#444}
</style>
</head>
<body>

<div class="abs topbar">
  <div class="abs contact">
    <span>&#9990;&nbsp; +41 44 000 12 34</span><span>|</span>
    <span><svg width="12" height="9" viewBox="0 0 12 9"><rect x=".5" y=".5" width="11" height="8" fill="none" stroke="#3ccf44"/><path d="M.5 .5l5.5 4 5.5-4" fill="none" stroke="#3ccf44"/></svg>&nbsp; info@kavrin.ch</span>
  </div>
  <div class="abs links">eCommerce &nbsp;|&nbsp; Online Marketing &nbsp;|&nbsp; Integration</div>
</div>

<header class="abs header">
  <div class="abs logo">KAVRIN</div>
  <nav class="abs nav">
    <span class="active">Home</span><span>About us</span><span>Blog</span><span>History</span><span>Customer References</span><span>Contact</span>
  </nav>
  <div class="btn book">&#9635;&nbsp;&nbsp;Book an appointment</div>
</header>

<section class="abs hero">
  <div class="photo" role="img" aria-label="Team working on laptops with digital marketing icons overlay"></div>
  <h1 class="serif">Your online marketing agency<br>in Zurich for SMEs</h1>
  <div class="btn b1">Offers</div>
  <div class="btn b2">Deadline</div>
  <svg class="abs" style="left:0;top:0" width="1200" height="600" viewBox="0 0 1200 600">
    <path d="M0,400 Q600,800 1200,395 L1200,600 L0,600 Z" fill="#fff"/>
    <path d="M0,400 Q600,800 1200,395" fill="none" stroke="#3ccf44" stroke-width="9"/>
  </svg>
  <div class="abs dots"><i></i><i class="on"></i><i></i><i></i></div>
</section>

<section class="intro">
  <h2 class="abs serif">The fast way to the<br>online shop</h2>
  <p class="abs body">Our goal is to give you added value with strategic online marketing – a technological competitive advantage that makes the difference. We build on automated processes for setting up and operating your online shop. In this way, we shorten project times, bring web shops online faster and simplify operations. This is how you get to your new web branch quickly and easily.</p>
  <div class="btn" style="left:112px;top:1168px;width:136px;height:44px">Read more</div>
  <div class="abs ring"><div class="photo" role="img" aria-label="Two colleagues looking at a tablet in an office"></div></div>
  <div class="abs badge"><span></span></div>
</section>

<section class="abs how">
  <h2 class="abs serif">How does it all work?<span class="rule center"></span></h2>
  <div class="abs card" style="left:120px">
    <h3>Your successful entry into<br>e-commerce</h3><span class="rule center" style="width:34px"></span>
    <p>Do you want to sell your products or services online? But as an SME, don't you have a marketing department with e-commerce know-how? Then you will face a series of questions that are critical to the success of your web business:</p>
    <p style="margin-top:12px">Which shop system is best suited to your goals?<br>Which online marketing measures really bring you something?<br>What technical and administrative effort is required at what cost? And which legal aspects have to be considered?<br>Only experienced e-commerce specialists can give you the answers – experienced online marketing professionals like Kavrin.</p>
  </div>
  <div class="abs card" style="left:612px">
    <h3>Our individual<br>online marketing solutions</h3><span class="rule center" style="width:34px"></span>
    <p>In us you will find a committed team with passion, professional skills and curiosity for all topics related to e-commerce and online marketing. Our agency gets you online with your project quickly, purposefully and economically.</p>
    <p style="margin-top:12px">Your advantage: We take care of the special field of online marketing for you - you have a free hand for your core competencies and the good feeling of having a reliable partner for the online expansion of your sales.</p>
  </div>
  <div class="abs icon" style="left:302px">
    <svg width="54" height="48" viewBox="0 0 54 48" fill="none" stroke="#fff" stroke-width="2"><rect x="10" y="4" width="36" height="26" rx="2"/><path d="M4 40h46M20 30v10M34 30v10"/><circle cx="14" cy="22" r="7"/><path d="M30 14h10M30 20h10"/></svg>
  </div>
  <div class="abs icon" style="left:794px">
    <svg width="54" height="48" viewBox="0 0 54 48" fill="none" stroke="#fff" stroke-width="2"><rect x="8" y="4" width="38" height="28" rx="2"/><path d="M4 40h46M27 32v8"/><path d="M16 24l7-8 6 5 9-10"/></svg>
  </div>
  <div class="btn cta">Contact us</div>
</section>

<section class="feature">
  <div class="abs frame" style="left:124px;top:2316px;width:462px;height:380px;border-right:none;border-bottom:none"></div>
  <div class="abs feat-photo" style="left:150px;top:2342px;width:462px;height:376px;background:linear-gradient(135deg,#b9a58d,#6f5a48 55%,#3a3029)" role="img" aria-label="Happy team gathered around a laptop"></div>
  <h2 class="abs serif" style="left:670px;top:2378px">Automates<br>more customers<span class="rule"></span></h2>
  <p class="abs body" style="left:670px;top:2496px;width:408px;text-align:justify">We help companies to sell products and services in their own online shop within 3 weeks. The result is more customers.</p>
  <div class="btn" style="left:670px;top:2608px;width:136px;height:46px">Learn more</div>

  <h2 class="abs serif" style="left:124px;top:2838px">Systematically<br>more sales<span class="rule"></span></h2>
  <p class="abs body" style="left:124px;top:2962px;width:408px">Do you have a shop, but no one shops there? Then use modern online marketing to be successful in a few months. We help you with that.</p>
  <div class="btn" style="left:124px;top:3072px;width:136px;height:45px">Learn more</div>
  <div class="abs frame" style="left:612px;top:2778px;width:463px;height:382px;border-left:none;border-bottom:none"></div>
  <div class="abs feat-photo" style="left:586px;top:2803px;width:464px;height:377px;background:linear-gradient(135deg,#d8dde0,#8a8f93 50%,#3c3a38)" role="img" aria-label="Man smiling while working on a laptop"></div>
</section>

<section class="abs partners">
  <h2 class="abs serif">Our partners<span class="rule center"></span></h2>
  <svg class="abs arrow" style="left:60px;top:215px" viewBox="0 0 30 30"><path d="M19 6l-9 9 9 9" fill="none" stroke="#fff" stroke-width="3"/></svg>
  <div class="abs plogo" style="left:146px"><i></i>Cartwell</div>
  <div class="abs plogo" style="left:333px"><i></i>Shopnest</div>
  <div class="abs plogo" style="left:519px"><i></i>Storelane</div>
  <div class="abs plogo" style="left:705px"><i></i>Trelby Ads</div>
  <div class="abs plogo" style="left:891px"><i></i>Mingle Ads</div>
  <svg class="abs arrow" style="left:1110px;top:215px" viewBox="0 0 30 30"><path d="M11 6l9 9-9 9" fill="none" stroke="#fff" stroke-width="3"/></svg>
</section>

<section class="team">
  <h2 class="abs serif">Kavrin team<span class="rule center"></span></h2>
  <div class="abs member" style="left:160px">
    <div class="photo" role="img" aria-label="Portrait of team member in a dark suit against a concrete wall"></div>
    <h4>Lukas Brenner</h4><span class="role">eCommerce Manager</span>
    <div class="social" style="left:336px"><i>&#9993;</i><i>in</i></div>
  </div>
  <div class="abs member" style="left:612px">
    <div class="photo" role="img" aria-label="Portrait of team member in a suit against a concrete wall"></div>
    <h4>Marco Feldmann</h4><span class="role">Online Marketing Manager</span>
    <div class="social" style="left:336px"><i>&#9993;</i><i>in</i></div>
  </div>
</section>

<section class="abs feedback">
  <h2 class="abs serif">Customer feedback<span class="rule center"></span></h2>
  <div class="abs review" style="left:108px">
    <div class="avatar" role="img" aria-label="Customer portrait"></div>
    <h5>Sabine Keller</h5><div class="stars">&#9733;&#9733;&#9733;&#9733;&#9733;</div><div class="quote">&rdquo;</div>
    <p>It fully meets my expectations. The cooperation was professional and uncomplicated. Again any time. Have already received several positive...</p>
  </div>
  <div class="abs review" style="left:444px">
    <div class="avatar" role="img" aria-label="Customer portrait"></div>
    <h5>Peter Hofer</h5><div class="stars">&#9733;&#9733;&#9733;&#9733;&#9733;</div><div class="quote">&rdquo;</div>
    <p>The agency helped me competently and comprehensively when I started my shop. I am very satisfied and can only recommend the team...</p>
  </div>
  <div class="abs review" style="left:775px">
    <div class="avatar" role="img" aria-label="Customer portrait"></div>
    <h5>Daniel Rossi</h5><div class="stars">&#9733;&#9733;&#9733;&#9733;&#9733;</div><div class="quote">&rdquo;</div>
    <p>Kavrin Marketing GmbH created my shop quickly and professionally. Despite time pressure, the shop was implemented with bravura...</p>
  </div>
</section>
<div class="abs circ" style="left:38px;border:2px solid var(--green)"><svg width="14" height="14" viewBox="0 0 14 14"><path d="M9 2L4 7l5 5" fill="none" stroke="#333" stroke-width="2"/></svg></div>
<div class="abs circ" style="left:1126px;background:var(--green)"><svg width="14" height="14" viewBox="0 0 14 14"><path d="M5 2l5 5-5 5" fill="none" stroke="#fff" stroke-width="2"/></svg></div>

<footer class="abs footer">
  <h6 style="left:112px">Get in touch</h6>
  <div class="field" style="top:108px">Your Name</div>
  <div class="field" style="top:155px">Your Email</div>
  <div class="field" style="top:203px">Subject</div>
  <div class="field" style="top:250px;height:63px">Your Message</div>
  <div class="btn" style="left:112px;top:331px;width:120px;height:34px;font-size:9px">Send message</div>

  <h6 style="left:458px">Navigation</h6>
  <ul style="left:458px"><li><i></i>Home</li><li><i></i>About Us</li><li><i></i>Blog</li><li><i></i>History</li><li><i></i>Customer References</li></ul>

  <h6 style="left:688px">Other links</h6>
  <ul style="left:688px"><li><i></i>eCommerce</li><li><i></i>Online Marketing</li><li><i></i>Integration</li><li><i></i>Contact</li></ul>

  <h6 style="left:898px">Contact info</h6>
  <div class="cinfo" style="top:112px"><svg width="10" height="13" viewBox="0 0 10 13"><path d="M5 12S1 7 1 4.5a4 4 0 018 0C9 7 5 12 5 12z" fill="#3ccf44"/><circle cx="5" cy="4.5" r="1.5" fill="#242424"/></svg><div style="padding-left:34px"><b>Address:</b>Lindenweg 12, 8004 Zurich,<br>Switzerland</div></div>
  <div class="cinfo" style="top:178px"><svg width="12" height="12" viewBox="0 0 12 12"><path d="M2 1l2.5 0 1 3-1.5 1a7 7 0 003 3l1-1.5 3 1V11C6 11 1 6 1 2z" fill="#3ccf44"/></svg><div style="padding-left:34px"><b>Phone:</b>+41 44 000 12 34</div></div>
  <div class="cinfo" style="top:234px"><svg width="13" height="10" viewBox="0 0 13 10"><rect width="13" height="10" fill="#3ccf44"/><path d="M0 0l6.5 5L13 0" fill="none" stroke="#242424"/></svg><div style="padding-left:34px"><b>Email:</b>info@kavrin.ch</div></div>

  <div class="abs divider"></div>
  <div class="abs copy">&copy; 2023 Kavrin &nbsp;- &nbsp;All Rights Reserved</div>
</footer>

</body>
</html>
```